Redesign Craft Brewing Recipe Website

Originally built with Bootstrap just to get the site going, I am seeking a complete redesign of the sites home page and recipe page. I am an experienced web developer with no graphic background, initially just looking for psd mocks.

I prefer styles that are clean and modern, and would prefer anything that is fun, engaging, and has an organic feel to it. I currently have a cartoon rabbit as a logo, but it needs some modification/tweaking, so any help in that area would be great as well.

Current site:
http://velvetfinch.cloudpagehost.net/

Current launch page/logo:
http://www.velvetfinch.com/

I like the overall layout of the elements currently, but the design sucks.

The launch page is at the following URL

Reason: Still looking for a more modern design. Designs received so far are too similar to the original.

My site is content based and does not contain images or products. Your design should not consist of large images.

Reason: The website has very little images, so the designs need to be more text and content based. The header needs to be very small and should not contain an ad rotater.

Target Market(s)

Home brewers, Craft brewers, Microbreweries, Brewpubs

Requirements
Must have
• Web 2.0 Look and Feel, Fun, Hip, Focus on content
Should not have
• A large photo as a header

```html
<!DOCTYPE html>
<html lang="en">
<head>
<meta charset="utf-8">
<title>Velvet Finch – Craft Beer Recipes</title>
<link href="https://fonts.googleapis.com/css2?family=Open+Sans:wght@400;600;700&family=Oswald:wght@500&display=swap" rel="stylesheet">
<style>
:root{
  --bar:#2e1a12;
  --header-a:#3b2417;
  --header-b:#9a5a2a;
  --cream:#efe8df;
  --white:#ffffff;
  --wood-a:#b0703a;
  --wood-b:#c48549;
  --wood-c:#a8663a;
  --text:#3a3a3a;
  --muted:#8a8a8a;
  --link:#b86a3a;
  --cell:#e9e9e9;
  --red:#c0341d;
  --orange:#e08a12;
  --blue:#1a8fd0;
  --teal:#1f9a8e;
  --green:#6cab17;
  --footer-band:#4a2a16;
}
*{box-sizing:border-box;margin:0;padding:0}
html,body{width:696px;height:1200px;overflow:hidden}
body{position:relative;font-family:"Open Sans",Arial,sans-serif;color:var(--text);background:var(--cream)}
.abs{position:absolute}

/* top bar */
.topbar{left:0;top:0;width:696px;height:18px;background:var(--bar)}
.search{left:82px;top:2px;width:115px;height:13px;background:var(--white);font-size:7px;color:var(--muted);padding:1px 3px;line-height:11px}
.search svg{position:absolute;right:3px;top:2px}
.nav{right:52px;top:3px;display:flex;gap:22px;font-size:8px;color:#e8ddd2}
.nav span:nth-child(2)::after{content:" ▾";font-size:6px}

/* header */
.header{left:0;top:18px;width:696px;height:102px;background:radial-gradient(ellipse at 50% 60%,var(--header-b),var(--header-a) 75%)}
.brand{left:0;top:40px;width:696px;display:flex;justify-content:center;align-items:center;gap:10px}
.brand-dot{display:block;width:22px;height:22px;border-radius:50%;background:var(--white)}
.brand-name{font-weight:600;font-size:26px;color:var(--white);line-height:30px}

/* tagline */
.tagline{left:0;top:120px;width:696px;height:26px;background:var(--cream);font-size:9.5px;color:#333}
.tagline p{position:absolute;left:200px;top:7px}
.share{position:absolute;top:7px;height:10px;border:1px solid #b9c4d8;background:#eef1f7;font-size:6px;line-height:8px;padding:0 3px;color:#3b5998}
.tag-sq{position:absolute;top:8px;width:9px;height:9px;background:#9a8f86}

/* filter bar */
.filters{left:0;top:146px;width:696px;height:34px;background:var(--white)}
.drop{position:absolute;top:6px;height:19px;background:#e3e3e3;border-radius:2px;font-size:8px;line-height:19px;padding-left:8px;color:#444}
.drop::after{content:"";position:absolute;right:8px;top:8px;border:4px solid transparent;border-top-color:#999}
.sort{left:523px;width:90px;background:var(--white);border:1px solid #ddd;font-size:7.5px;padding-left:5px;line-height:17px}
.sort::after{right:4px;top:7px;border-width:3.5px;border-top-color:var(--red)}
.sort b{color:var(--red);font-weight:600}

/* wood */
.wood{left:0;top:180px;width:696px;height:948px;
  background:repeating-linear-gradient(90deg,var(--wood-a) 0 62px,var(--wood-b) 62px 120px,var(--wood-c) 120px 176px,var(--wood-b) 176px 232px)}

/* recipe grid */
.grid{left:83px;top:194px;display:grid;grid-template-columns:repeat(4,124px);grid-auto-rows:214px;column-gap:11px;row-gap:9px}
.card{position:relative;background:var(--white);box-shadow:0 1px 3px rgba(0,0,0,.35)}
.photo{position:absolute;left:6px;top:5px;width:112px;height:112px}
.photo-title{position:absolute;left:0;bottom:5px;width:100%;height:13px;background:rgba(20,10,5,.55);color:#fff;font-size:7.5px;line-height:13px;text-align:center}
.counts{position:absolute;left:6px;top:121px;display:flex;gap:2px}
.count{width:15px;height:22px;background:var(--cell);text-align:center;font-size:6.5px;color:#666;padding-top:2px;line-height:9px}
.count svg{display:block;margin:0 auto}
.method{position:absolute;right:6px;top:121px;height:9px;padding:0 5px;font-size:6.5px;line-height:9px;color:#fff}
.style{position:absolute;right:6px;top:131px;width:63px;height:11px;background:#f0f0f0;font-size:6.5px;line-height:11px;text-align:right;padding-right:3px;color:#777}
.desc{position:absolute;left:6px;top:148px;width:112px;font-size:7px;line-height:10px}
.by{position:absolute;left:6px;top:171px;font-size:7px;color:#555}
.by a{color:var(--link);text-decoration:none}
.stats{position:absolute;left:2px;top:188px;display:flex;gap:1px}
.stat{width:22px;height:23px;background:var(--cell);font-size:6.2px;line-height:10px;text-align:center;padding-top:2px;color:#444}
.stat.srm{color:#fff;width:24px}
.extract{background:var(--red)}.partial{background:var(--orange)}.allgrain{background:var(--blue)}
.srm-red{background:var(--red)}.srm-teal{background:var(--teal)}.srm-green{background:var(--green)}.srm-blue{background:var(--blue)}
.p1{background:linear-gradient(160deg,#c9c27a,#d79a2a 55%,#7a4a12)}
.p2{background:linear-gradient(160deg,#2a1a10,#8a5020 60%,#d89a40)}
.p3{background:linear-gradient(160deg,#3a2010,#b04a15 55%,#e0a040)}
.p4{background:linear-gradient(170deg,#3a200e,#d08a2a 55%,#f0c070)}
.p5{background:linear-gradient(160deg,#f4ece0,#c88a3a 60%,#6a3a10)}
.p6{background:linear-gradient(160deg,#5a2a0a,#c85a10 55%,#e8a040)}
.p7{background:linear-gradient(160deg,#aab060,#e0c070 55%,#c08a30)}
.p8{background:linear-gradient(160deg,#4a3010,#d8a040 55%,#f4e0a0)}
.p9{background:linear-gradient(170deg,#5a1a10,#c06020 55%,#e8b050)}
.p10{background:linear-gradient(160deg,#1a0a05,#a05010 55%,#e8a030)}
.p11{background:linear-gradient(160deg,#3a1a0a,#b8501a 55%,#d88a30)}
.p12{background:linear-gradient(160deg,#201008,#b85a18 55%,#e89a40)}
.p13{background:linear-gradient(160deg,#3a2a20,#2a7ad0 45%,#d8a030)}
.p14{background:linear-gradient(160deg,#c06010,#e08a20 55%,#a04a10)}
.p15{background:linear-gradient(160deg,#f4ece0,#d89a40 55%,#7a4a18)}
.p16{background:linear-gradient(160deg,#2a1a10,#a05020 55%,#3a1a0a)}

/* footer */
.footer-band{left:0;top:1128px;width:696px;height:20px;background:var(--footer-band)}
.footer-brand{left:0;top:1100px;width:696px;display:flex;justify-content:center;align-items:center;gap:6px}
.footer-brand .brand-dot{width:14px;height:14px}
.footer-brand .brand-name{font-size:15px;line-height:20px}
.footer-art{left:528px;top:1080px;width:78px;height:54px;border-radius:6px;background:linear-gradient(90deg,#c8781e,#8a2a10 50%,#e0a040)}
.mailing{left:86px;top:1148px;width:522px;height:28px;background:var(--white)}
.mailing h2{position:absolute;left:5px;top:5px;font-family:"Oswald",Arial,sans-serif;font-weight:500;font-size:13px;color:var(--red);letter-spacing:.2px}
.mailing p{position:absolute;left:130px;top:9px;font-size:7px;color:#444}
.email{position:absolute;left:286px;top:7px;width:104px;height:14px;border:1px solid #ccc;border-radius:8px;font-size:7px;line-height:12px;padding-left:8px;color:#777}
.join{position:absolute;left:382px;top:6px;width:22px;height:16px;border-radius:8px;background:#e07a20;font-size:6px;color:#fff;line-height:16px;text-align:center;font-weight:700}
.connect{position:absolute;left:408px;top:9px;font-size:7px;font-style:italic;font-weight:600;color:#444}
.social-sq{position:absolute;top:7px;width:14px;height:14px;border-radius:2px}
.copyright{left:0;top:1182px;width:696px;text-align:center;font-size:7px;color:var(--link)}
</style>
</head>
<body>
<svg width="0" height="0" style="position:absolute">
  <defs>
    <symbol id="i-heart" viewBox="0 0 10 10"><path d="M5 9 1 5a2.2 2.2 0 0 1 4-3 2.2 2.2 0 0 1 4 3z" fill="#9a9a9a"/></symbol>
    <symbol id="i-fork" viewBox="0 0 10 10"><path d="M2 2h3v6H2zM5 4h4v2H5z" fill="#9a9a9a"/></symbol>
    <symbol id="i-star" viewBox="0 0 10 10"><path d="M5 .8 6.3 3.7 9.4 4 7 6.1 7.7 9.2 5 7.6 2.3 9.2 3 6.1.6 4l3.1-.3z" fill="#9a9a9a"/></symbol>
  </defs>
</svg>

<div class="abs topbar"></div>
<div class="abs search">Search<svg width="8" height="8" viewBox="0 0 10 10"><circle cx="4" cy="4" r="3" fill="none" stroke="#333" stroke-width="1.5"/><path d="M6 6l3 3" stroke="#333" stroke-width="1.5"/></svg></div>
<nav class="abs nav"><span>Recipes</span><span>About</span><span>Login</span></nav>

<header class="abs header" role="img" aria-label="Blurred photo of beer glasses on a bar"></header>
<div class="abs brand"><span class="brand-dot"></span><span class="brand-name">Velvet Finch</span></div>

<div class="abs tagline">
  <p>Velvet Finch is the easiest way to create and share craft beer recipes.</p>
  <span class="share" style="left:508px">Like 0</span>
  <span class="share" style="left:552px">Send</span>
  <span class="tag-sq" style="left:586px"></span>
  <span class="tag-sq" style="left:602px"></span>
</div>

<div class="abs filters">
  <div class="drop" style="left:82px;width:73px">Brewing</div>
  <div class="drop" style="left:160px;width:73px">Styles</div>
  <div class="drop" style="left:238px;width:74px">Match Maker</div>
  <div class="drop sort">Sort by <b>&gt; Trending</b></div>
</div>

<div class="abs wood" role="img" aria-label="Wooden plank texture"></div>

<main class="abs grid">
<article class="card"><div class="photo p1" role="img" aria-label="Beer poured into glass"><div class="photo-title">Oak Bastard Sweet Mead</div></div>
<div class="counts"><div class="count"><svg width="8" height="8"><use href="#i-heart"/></svg>10</div><div class="count"><svg width="8" height="8"><use href="#i-fork"/></svg>9</div><div class="count"><svg width="8" height="8"><use href="#i-star"/></svg>0</div></div>
<div class="method extract">Extract</div><div class="style">Belgian Tripel</div>
<p class="desc">Lorem ipsum dolor sit amet, consectetur adipisicing elit.</p><p class="by">Created by <a href="#">Dana Whitfield</a></p>
<div class="stats"><div class="stat">2.24%<br>ABV</div><div class="stat">24<br>IBU</div><div class="stat">1.006<br>FG</div><div class="stat">1.022<br>OG</div><div class="stat srm srm-red">4<br>SRM</div></div></article>

<article class="card"><div class="photo p2" role="img" aria-label="Beer glasses by a barrel"><div class="photo-title">Oak Bastard Sweet Mead</div></div>
<div class="counts"><div class="count"><svg width="8" height="8"><use href="#i-heart"/></svg>8</div><div class="count"><svg width="8" height="8"><use href="#i-fork"/></svg>15</div><div class="count"><svg width="8" height="8"><use href="#i-star"/></svg>0</div></div>
<div class="method partial">PartialMash</div><div class="style">Mild</div>
<p class="desc">Lorem ipsum dolor sit amet, consectetur adipisicing elit.</p><p class="by">Created by <a href="#">Dana Whitfield</a></p>
<div class="stats"><div class="stat">2.24%<br>ABV</div><div class="stat">24<br>IBU</div><div class="stat">1.006<br>FG</div><div class="stat">1.022<br>OG</div><div class="stat srm srm-teal">4<br>SRM</div></div></article>

<article class="card"><div class="photo p3" role="img" aria-label="Two amber beers at a bar"><div class="photo-title">Oak Bastard Sweet Mead</div></div>
<div class="counts"><div class="count"><svg width="8" height="8"><use href="#i-heart"/></svg>6</div><div class="count"><svg width="8" height="8"><use href="#i-fork"/></svg>3</div><div class="count"><svg width="8" height="8"><use href="#i-star"/></svg>0</div></div>
<div class="method allgrain">AllGrain</div><div class="style">Belgian Tripel</div>
<p class="desc">Lorem ipsum dolor sit amet, consectetur adipisicing elit.</p><p class="by">Created by <a href="#">Dana Whitfield</a></p>
<div class="stats"><div class="stat">2.24%<br>ABV</div><div class="stat">24<br>IBU</div><div class="stat">1.006<br>FG</div><div class="stat">1.022<br>OG</div><div class="stat srm srm-green">4<br>SRM</div></div></article>

<article class="card"><div class="photo p4" role="img" aria-label="Glass of lager with foam"><div class="photo-title">Oak Bastard Sweet Mead</div></div>
<div class="counts"><div class="count"><svg width="8" height="8"><use href="#i-heart"/></svg>2</div><div class="count"><svg width="8" height="8"><use href="#i-fork"/></svg>9</div><div class="count"><svg width="8" height="8"><use href="#i-star"/></svg>0</div></div>
<div class="method extract">Extract</div><div class="style">Belgian Tripel</div>
<p class="desc">Lorem ipsum dolor sit amet, consectetur adipisicing elit.</p><p class="by">Created by <a href="#">Dana Whitfield</a></p>
<div class="stats"><div class="stat">2.24%<br>ABV</div><div class="stat">24<br>IBU</div><div class="stat">1.006<br>FG</div><div class="stat">1.022<br>OG</div><div class="stat srm srm-blue">4<br>SRM</div></div></article>

<article class="card"><div class="photo p5" role="img" aria-label="Beer glasses with barrel and wheat"><div class="photo-title">Oak Bastard Sweet Mead</div></div>
<div class="counts"><div class="count"><svg width="8" height="8"><use href="#i-heart"/></svg>5</div><div class="count"><svg width="8" height="8"><use href="#i-fork"/></svg>20</div><div class="count"><svg width="8" height="8"><use href="#i-star"/></svg>0</div></div>
<div class="method allgrain">AllGrain</div><div class="style">Belgian Tripel</div>
<p class="desc">Lorem ipsum dolor sit amet, consectetur adipisicing elit.</p><p class="by">Created by <a href="#">Dana Whitfield</a></p>
<div class="stats"><div class="stat">2.24%<br>ABV</div><div class="stat">24<br>IBU</div><div class="stat">1.006<br>FG</div><div class="stat">1.022<br>OG</div><div class="stat srm srm-blue">4<br>SRM</div></div></article>

<article class="card"><div class="photo p6" role="img" aria-label="Two glasses of amber ale"><div class="photo-title">Oak Bastard Sweet Mead</div></div>
<div class="counts"><div class="count"><svg width="8" height="8"><use href="#i-heart"/></svg>0</div><div class="count"><svg width="8" height="8"><use href="#i-fork"/></svg>6</div><div class="count"><svg width="8" height="8"><use href="#i-star"/></svg>0</div></div>
<div class="method extract">Extract</div><div class="style">Munich Helles</div>
<p class="desc">Lorem ipsum dolor sit amet, consectetur adipisicing elit.</p><p class="by">Created by <a href="#">Dana Whitfield</a></p>
<div class="stats"><div class="stat">2.24%<br>ABV</div><div class="stat">24<br>IBU</div><div class="stat">1.006<br>FG</div><div class="stat">1.022<br>OG</div><div class="stat srm srm-red">4<br>SRM</div></div></article>

<article class="card"><div class="photo p7" role="img" aria-label="Beer pouring from a tap"><div class="photo-title">Oak Bastard Sweet Mead</div></div>
<div class="counts"><div class="count"><svg width="8" height="8"><use href="#i-heart"/></svg>3</div><div class="count"><svg width="8" height="8"><use href="#i-fork"/></svg>8</div><div class="count"><svg width="8" height="8"><use href="#i-star"/></svg>0</div></div>
<div class="method partial">PartialMash</div><div class="style">Mild</div>
<p class="desc">Lorem ipsum dolor sit amet, consectetur adipisicing elit.</p><p class="by">Created by <a href="#">Dana Whitfield</a></p>
<div class="stats"><div class="stat">2.24%<br>ABV</div><div class="stat">24<br>IBU</div><div class="stat">1.006<br>FG</div><div class="stat">1.022<br>OG</div><div class="stat srm srm-teal">4<br>SRM</div></div></article>

<article class="card"><div class="photo p8" role="img" aria-label="Beer mugs on a wooden table"><div class="photo-title">Oak Bastard Sweet Mead</div></div>
<div class="counts"><div class="count"><svg width="8" height="8"><use href="#i-heart"/></svg>2</div><div class="count"><svg width="8" height="8"><use href="#i-fork"/></svg>10</div><div class="count"><svg width="8" height="8"><use href="#i-star"/></svg>0</div></div>
<div class="method allgrain">AllGrain</div><div class="style">Belgian Tripel</div>
<p class="desc">Lorem ipsum dolor sit amet, consectetur adipisicing elit.</p><p class="by">Created by <a href="#">Dana Whitfield</a></p>
<div class="stats"><div class="stat">2.24%<br>ABV</div><div class="stat">24<br>IBU</div><div class="stat">1.006<br>FG</div><div class="stat">1.022<br>OG</div><div class="stat srm srm-green">4<br>SRM</div></div></article>

<article class="card"><div class="photo p9" role="img" aria-label="Pint of ale with thick foam"><div class="photo-title">Oak Bastard Sweet Mead</div></div>
<div class="counts"><div class="count"><svg width="8" height="8"><use href="#i-heart"/></svg>8</div><div class="count"><svg width="8" height="8"><use href="#i-fork"/></svg>6</div><div class="count"><svg width="8" height="8"><use href="#i-star"/></svg>0</div></div>
<div class="method partial">PartialMash</div><div class="style">Mild</div>
<p class="desc">Lorem ipsum dolor sit amet, consectetur adipisicing elit.</p><p class="by">Created by <a href="#">Dana Whitfield</a></p>
<div class="stats"><div class="stat">2.24%<br>ABV</div><div class="stat">24<br>IBU</div><div class="stat">1.006<br>FG</div><div class="stat">1.022<br>OG</div><div class="stat srm srm-teal">4<br>SRM</div></div></article>

<article class="card"><div class="photo p10" role="img" aria-label="Beer mug in warm light"><div class="photo-title">Oak Bastard Sweet Mead</div></div>
<div class="counts"><div class="count"><svg width="8" height="8"><use href="#i-heart"/></svg>5</div><div class="count"><svg width="8" height="8"><use href="#i-fork"/></svg>0</div><div class="count"><svg width="8" height="8"><use href="#i-star"/></svg>0</div></div>
<div class="method allgrain">AllGrain</div><div class="style">English Cider</div>
<p class="desc">Lorem ipsum dolor sit amet, consectetur adipisicing elit.</p><p class="by">Created by <a href="#">Dana Whitfield</a></p>
<div class="stats"><div class="stat">2.24%<br>ABV</div><div class="stat">24<br>IBU</div><div class="stat">1.006<br>FG</div><div class="stat">1.022<br>OG</div><div class="stat srm srm-blue">4<br>SRM</div></div></article>

<article class="card"><div class="photo p11" role="img" aria-label="Two amber beers at a bar"><div class="photo-title">Oak Bastard Sweet Mead</div></div>
<div class="counts"><div class="count"><svg width="8" height="8"><use href="#i-heart"/></svg>4</div><div class="count"><svg width="8" height="8"><use href="#i-fork"/></svg>3</div><div class="count"><svg width="8" height="8"><use href="#i-star"/></svg>0</div></div>
<div class="method extract">Extract</div><div class="style">Belgian Tripel</div>
<p class="desc">Lorem ipsum dolor sit amet, consectetur adipisicing elit.</p><p class="by">Created by <a href="#">Dana Whitfield</a></p>
<div class="stats"><div class="stat">2.24%<br>ABV</div><div class="stat">24<br>IBU</div><div class="stat">1.006<br>FG</div><div class="stat">1.022<br>OG</div><div class="stat srm srm-green">4<br>SRM</div></div></article>

<article class="card"><div class="photo p12" role="img" aria-label="Beers in front of bar shelves"><div class="photo-title">Oak Bastard Sweet Mead</div></div>
<div class="counts"><div class="count"><svg width="8" height="8"><use href="#i-heart"/></svg>2</div><div class="count"><svg width="8" height="8"><use href="#i-fork"/></svg>11</div><div class="count"><svg width="8" height="8"><use href="#i-star"/></svg>0</div></div>
<div class="method extract">Extract</div><div class="style">Belgian Tripel</div>
<p class="desc">Lorem ipsum dolor sit amet, consectetur adipisicing elit.</p><p class="by">Created by <a href="#">Dana Whitfield</a></p>
<div class="stats"><div class="stat">2.24%<br>ABV</div><div class="stat">24<br>IBU</div><div class="stat">1.006<br>FG</div><div class="stat">1.022<br>OG</div><div class="stat srm srm-red">4<br>SRM</div></div></article>

<article class="card"><div class="photo p13" role="img" aria-label="Assorted cocktail and beer glasses"><div class="photo-title">Oak Bastard Sweet Mead</div></div>
<div class="counts"><div class="count"><svg width="8" height="8"><use href="#i-heart"/></svg>8</div><div class="count"><svg width="8" height="8"><use href="#i-fork"/></svg>14</div><div class="count"><svg width="8" height="8"><use href="#i-star"/></svg>0</div></div>
<div class="method extract">Extract</div><div class="style">Mild</div>
<p class="desc">Lorem ipsum dolor sit amet, consectetur adipisicing elit.</p><p class="by">Created by <a href="#">Dana Whitfield</a></p>
<div class="stats"><div class="stat">2.24%<br>ABV</div><div class="stat">24<br>IBU</div><div class="stat">1.006<br>FG</div><div class="stat">1.022<br>OG</div><div class="stat srm srm-teal">4<br>SRM</div></div></article>

<article class="card"><div class="photo p14" role="img" aria-label="Close-up of beer pouring"><div class="photo-title">Oak Bastard Sweet Mead</div></div>
<div class="counts"><div class="count"><svg width="8" height="8"><use href="#i-heart"/></svg>7</div><div class="count"><svg width="8" height="8"><use href="#i-fork"/></svg>50</div><div class="count"><svg width="8" height="8"><use href="#i-star"/></svg>0</div></div>
<div class="method extract">Extract</div><div class="style">Belgian Tripel</div>
<p class="desc">Lorem ipsum dolor sit amet, consectetur adipisicing elit.</p><p class="by">Created by <a href="#">Dana Whitfield</a></p>
<div class="stats"><div class="stat">2.24%<br>ABV</div><div class="stat">24<br>IBU</div><div class="stat">1.006<br>FG</div><div class="stat">1.022<br>OG</div><div class="stat srm srm-green">4<br>SRM</div></div></article>

<article class="card"><div class="photo p15" role="img" aria-label="Beer glasses with barrel and wheat"><div class="photo-title">Oak Bastard Sweet Mead</div></div>
<div class="counts"><div class="count"><svg width="8" height="8"><use href="#i-heart"/></svg>4</div><div class="count"><svg width="8" height="8"><use href="#i-fork"/></svg>20</div><div class="count"><svg width="8" height="8"><use href="#i-star"/></svg>0</div></div>
<div class="method allgrain">AllGrain</div><div class="style">English Cider</div>
<p class="desc">Lorem ipsum dolor sit amet, consectetur adipisicing elit.</p><p class="by">Created by <a href="#">Dana Whitfield</a></p>
<div class="stats"><div class="stat">2.24%<br>ABV</div><div class="stat">24<br>IBU</div><div class="stat">1.006<br>FG</div><div class="stat">1.022<br>OG</div><div class="stat srm srm-blue">4<br>SRM</div></div></article>

<article class="card"><div class="photo p16" role="img" aria-label="Row of dark and amber beers"><div class="photo-title">Oak Bastard Sweet Mead</div></div>
<div class="counts"><div class="count"><svg width="8" height="8"><use href="#i-heart"/></svg>2</div><div class="count"><svg width="8" height="8"><use href="#i-fork"/></svg>8</div><div class="count"><svg width="8" height="8"><use href="#i-star"/></svg>0</div></div>
<div class="method partial">PartialMash</div><div class="style">Belgian Tripel</div>
<p class="desc">Lorem ipsum dolor sit amet, consectetur adipisicing elit.</p><p class="by">Created by <a href="#">Dana Whitfield</a></p>
<div class="stats"><div class="stat">2.24%<br>ABV</div><div class="stat">24<br>IBU</div><div class="stat">1.006<br>FG</div><div class="stat">1.022<br>OG</div><div class="stat srm srm-red">4<br>SRM</div></div></article>
</main>

<div class="abs footer-band"></div>
<div class="abs footer-brand"><span class="brand-dot"></span><span class="brand-name">Velvet Finch</span></div>
<div class="abs footer-art" role="img" aria-label="Illustration of beer mugs with hops"></div>

<section class="abs mailing">
  <h2>JOIN OUR MAILING LIST</h2>
  <p>Sign up for our e-mail list to receive updates</p>
  <div class="email">Your e-mail address</div>
  <div class="join">JOIN</div>
  <span class="connect">Connect with us on</span>
  <span class="social-sq" style="left:474px;background:#3aa3d8"></span>
  <span class="social-sq" style="left:490px;background:#3b5a98"></span>
  <span class="social-sq" style="left:506px;background:#1c78b4"></span>
</section>
<p class="abs copyright">Copyright © 2013 Velvet Finch. All rights reserved.</p>
</body>
</html>
```